Design a poster that illustrates the six central pillars of our school district's efforts with students. The attached PDF outlines the six main competencies we aim for students to possess upon graduation. Each of the 6 has 3 bullet points for the poster as well. The title is "Profile of a Trailblazer". Our mascot is this attached winged wheel. The overall concept is that staff take kids when they are young and develop these 6 things when they graduate. Our colors are navy, red, and white. We will make this poster in a variety of sizes in offices, classrooms, and in digital spaces as well. On the PDF - ignore the column that says "Synthesis". That has nothing to do with this poster.

The district is Harlow Creek Public Schools https://www.harlowcreek-schools.example/

```html
<!DOCTYPE html>
<html lang="en">
<head>
<meta charset="utf-8">
<title>Profile of a Trailblazer – Harlow Creek Public Schools</title>
<link rel="stylesheet" href="https://fonts.googleapis.com/css2?family=Inter:wght@400;500&family=Montserrat:wght@700;800&family=Outfit:wght@400;500;600&display=swap">
<style>
  :root{
    --navy:#1f2b46;
    --navy-light:#2b3d63;
    --red:#a31d25;
    --red-dark:#7c1519;
    --ink:#2a2d38;
    --panel:#e9e9eb;
    --paper:#f8f8f9;
    --pillar-light:#dcdde2;
    --pillar-dark:#bfc0ca;
    --backdrop:#8f8f8f;
  }
  *{margin:0;padding:0;box-sizing:border-box}
  html,body{width:984px;height:1200px;overflow:hidden}
  body{background:var(--backdrop);position:relative;font-family:"Outfit",sans-serif;color:var(--ink)}
  .poster{position:absolute;left:77px;top:86px;width:806px;height:1042px;
    background:linear-gradient(160deg,#ffffff 0%,var(--paper) 55%,#f1f1f3 100%);overflow:hidden}
  .hero-photo{position:absolute;left:0;top:0;width:806px;height:184px;
    background:linear-gradient(180deg,#3d5a34 0%,#4c6a44 40%,#2c3a5c 75%,#7d8a96 100%)}
  .header-art{position:absolute;left:0;top:0}
  .district{position:absolute;left:530px;top:173px;font-family:"Inter",sans-serif;color:var(--navy)}
  .district-name{font-size:19.5px;font-weight:500;display:flex;align-items:center;gap:10px}
  .district-name::before{content:"";width:14px;height:14px;border-radius:50%;background:var(--red);margin-left:-26px;margin-right:2px}
  .district-tagline{font-size:12.6px;font-weight:400;margin-top:5px;color:#1b1f2c}
  .frame-lines{position:absolute;left:0;top:0}
  .title{position:absolute;left:-226px;top:584px;width:592px;height:44px;line-height:44px;
    text-align:center;white-space:nowrap;transform:rotate(-90deg);
    font-family:"Montserrat",sans-serif;font-weight:800;font-size:35px;color:var(--navy)}
  .title .accent{color:var(--red)}
  .pillar{position:absolute;left:0;top:0}
  .trait{position:absolute;left:0;width:806px;height:110px}
  .trait svg{position:absolute;left:0;top:0}
  .trait-name{position:absolute;left:248px;top:1px;font-size:18.5px;font-weight:600;color:#fff;line-height:26px}
  .trait-points{position:absolute;top:38px;left:0;width:806px}
  .point{position:absolute;font-size:12px;line-height:15px;color:var(--ink);padding-left:9px}
  .point::before{content:"";position:absolute;left:-8px;top:4px;width:6px;height:6px;
    border:1.4px solid var(--red);transform:rotate(45deg)}
  .p1{left:252px;width:144px}
  .p2{left:427px;width:144px}
  .p3{left:596px;width:182px}
  .footer{position:absolute;left:0;bottom:0;width:806px;height:63px;background:var(--navy);
    display:flex;align-items:center;justify-content:space-between;padding:0 28px 0 36px;
    color:#fff;font-size:14.5px;font-weight:400}
  .footer-item{display:flex;align-items:center;gap:7px;white-space:nowrap}
  .icon{fill:none;stroke:#fff;stroke-width:1.3;stroke-linecap:round;stroke-linejoin:round}
</style>
</head>
<body>
<div class="poster">
  <div class="hero-photo" role="img" aria-label="Marching band students in navy shirts carrying flags and instruments outdoors"></div>

  <svg class="header-art" width="806" height="245" viewBox="0 0 806 245">
    <polygon points="379,145 806,145 806,236 437,236 400,184" fill="var(--panel)"/>
    <polyline points="0,184.5 400,184.5 437,236 806,236" fill="none" stroke="var(--red)" stroke-width="4"/>
  </svg>
  <div class="district">
    <div class="district-name">Harlow Creek Public Schools</div>
    <div class="district-tagline">Excellence in Academics, Arts &amp; Athletics</div>
  </div>

  <svg class="frame-lines" width="806" height="1042" viewBox="0 0 806 1042">
    <line x1="67" y1="274" x2="67" y2="314" stroke="var(--navy)" stroke-width="2"/>
    <polyline points="67,898 67,968 806,968" fill="none" stroke="var(--navy)" stroke-width="2"/>
  </svg>
  <div class="title">PROFILE OF A <span class="accent">TRAILBLAZER</span></div>

  <svg class="pillar" width="806" height="1042" viewBox="0 0 806 1042">
    <polygon points="139,243 181,210 181,972 139,972" fill="var(--pillar-light)"/>
    <polygon points="181,210 223,243 223,972 181,972" fill="var(--pillar-dark)"/>
  </svg>

  <!-- 01 -->
  <div class="trait" style="top:274px">
    <svg width="806" height="100" viewBox="0 0 806 100">
      <polygon points="131,7 181,24 181,78 131,61" fill="var(--red)"/>
      <polygon points="181,24 232,3 232,57 181,78" fill="var(--red-dark)"/>
      <polygon points="227,0 236,0 236,8" fill="#5a0f13"/>
      <polygon points="236,0 420,0 406,29 236,29" fill="var(--red-dark)"/>
      <line x1="425" y1="13" x2="415" y2="29" stroke="#c9a9a9" stroke-width="1.5"/>
      <line x1="415" y1="28.5" x2="757" y2="28.5" stroke="var(--red)" stroke-width="1"/>
      <text x="139" y="53" font-family="Outfit, sans-serif" font-weight="600" font-size="23" fill="#fff">01</text>
      <g class="icon" transform="translate(194,26)">
        <rect x="0" y="2" width="14" height="9" rx="1.5"/><path d="M3 11l-1 4 4-4"/>
        <rect x="11" y="10" width="13" height="9" rx="1.5"/><path d="M20 19l1 4-4-4"/>
        <line x1="3" y1="5.5" x2="11" y2="5.5"/><line x1="14" y1="14.5" x2="21" y2="14.5"/>
      </g>
      <line x1="406" y1="42" x2="406" y2="88" stroke="var(--red)" stroke-dasharray="1.5 3"/>
      <line x1="577" y1="42" x2="577" y2="88" stroke="var(--red)" stroke-dasharray="1.5 3"/>
    </svg>
    <div class="trait-name">Communicator</div>
    <div class="trait-points">
      <p class="point p1">Expresses ideas clearly and respectfully (written &amp; verbal).</p>
      <p class="point p2">Listens actively and understands diverse perspectives.</p>
      <p class="point p3">Adjusts communication to suit the audience and context.</p>
    </div>
  </div>

  <!-- 02 -->
  <div class="trait" style="top:385px">
    <svg width="806" height="100" viewBox="0 0 806 100">
      <polygon points="131,7 181,24 181,78 131,61" fill="var(--navy)"/>
      <polygon points="181,24 232,3 232,57 181,78" fill="var(--navy-light)"/>
      <polygon points="227,0 236,0 236,8" fill="#111a2c"/>
      <polygon points="236,0 420,0 406,29 236,29" fill="var(--navy)"/>
      <line x1="425" y1="13" x2="415" y2="29" stroke="#aab0c0" stroke-width="1.5"/>
      <line x1="415" y1="28.5" x2="757" y2="28.5" stroke="var(--navy)" stroke-width="1"/>
      <text x="139" y="53" font-family="Outfit, sans-serif" font-weight="600" font-size="23" fill="#fff">02</text>
      <g class="icon" transform="translate(196,24)">
        <circle cx="11" cy="8" r="4"/><circle cx="11" cy="8" r="7" stroke-dasharray="2.5 2"/>
        <path d="M7 16c0 2 1 3 1 5h6c0-2 1-3 1-5"/><line x1="8.5" y1="24" x2="13.5" y2="24"/>
      </g>
      <line x1="406" y1="42" x2="406" y2="88" stroke="var(--red)" stroke-dasharray="1.5 3"/>
      <line x1="577" y1="42" x2="577" y2="88" stroke="var(--red)" stroke-dasharray="1.5 3"/>
    </svg>
    <div class="trait-name">Critical Thinker</div>
    <div class="trait-points">
      <p class="point p1">Questions, analyzes, and evaluates information from multiple sources.</p>
      <p class="point p2">Identifies and solves complex problems creatively.</p>
      <p class="point p3">Uses evidence and diverse perspectives to form reasoned conclusions and make informed decisions.</p>
    </div>
  </div>

  <!-- 03 -->
  <div class="trait" style="top:496px">
    <svg width="806" height="100" viewBox="0 0 806 100">
      <polygon points="131,7 181,24 181,78 131,61" fill="var(--red)"/>
      <polygon points="181,24 232,3 232,57 181,78" fill="var(--red-dark)"/>
      <polygon points="227,0 236,0 236,8" fill="#5a0f13"/>
      <polygon points="236,0 420,0 406,29 236,29" fill="var(--red-dark)"/>
      <line x1="425" y1="13" x2="415" y2="29" stroke="#c9a9a9" stroke-width="1.5"/>
      <line x1="415" y1="28.5" x2="757" y2="28.5" stroke="var(--red)" stroke-width="1"/>
      <text x="139" y="53" font-family="Outfit, sans-serif" font-weight="600" font-size="23" fill="#fff">03</text>
      <g class="icon" transform="translate(194,22)">
        <circle cx="14" cy="7" r="3"/><circle cx="14" cy="7" r="6" stroke-dasharray="2.5 2"/>
        <path d="M1 22l5-4h7l4 2 7-5"/><path d="M6 18l3-2h6"/>
      </g>
      <line x1="406" y1="42" x2="406" y2="88" stroke="var(--red)" stroke-dasharray="1.5 3"/>
      <line x1="577" y1="42" x2="577" y2="88" stroke="var(--red)" stroke-dasharray="1.5 3"/>
    </svg>
    <div class="trait-name">Responsible</div>
    <div class="trait-points">
      <p class="point p1">Takes ownership of actions, choices, and commitments.</p>
      <p class="point p2">Manages time, resources, and self to meet expectations.</p>
      <p class="point p3">Acts with integrity and advocates for self and others.</p>
    </div>
  </div>

  <!-- 04 -->
  <div class="trait" style="top:607px">
    <svg width="806" height="100" viewBox="0 0 806 100">
      <polygon points="131,7 181,24 181,78 131,61" fill="var(--navy)"/>
      <polygon points="181,24 232,3 232,57 181,78" fill="var(--navy-light)"/>
      <polygon points="227,0 236,0 236,8" fill="#111a2c"/>
      <polygon points="236,0 420,0 406,29 236,29" fill="var(--navy)"/>
      <line x1="425" y1="13" x2="415" y2="29" stroke="#aab0c0" stroke-width="1.5"/>
      <line x1="415" y1="28.5" x2="757" y2="28.5" stroke="var(--navy)" stroke-width="1"/>
      <text x="139" y="53" font-family="Outfit, sans-serif" font-weight="600" font-size="23" fill="#fff">04</text>
      <g class="icon" transform="translate(195,24)">
        <circle cx="12" cy="12" r="4"/><circle cx="12" cy="12" r="10" stroke-dasharray="3 2.5"/>
        <rect x="10" y="-1" width="4" height="4"/><path d="M21 16l3 4h-5z"/><circle cx="3" cy="20" r="2"/>
      </g>
      <line x1="406" y1="42" x2="406" y2="88" stroke="var(--red)" stroke-dasharray="1.5 3"/>
      <line x1="577" y1="42" x2="577" y2="88" stroke="var(--red)" stroke-dasharray="1.5 3"/>
    </svg>
    <div class="trait-name">Adaptable</div>
    <div class="trait-points">
      <p class="point p1">Responds productively to new situations, challenges, and feedback.</p>
      <p class="point p2">Learns from new experiences and applies prior knowledge in evolving contexts.</p>
      <p class="point p3">Adjusts behavior and approach to effectively engage with diverse groups and environments.</p>
    </div>
  </div>

  <!-- 05 -->
  <div class="trait" style="top:718px">
    <svg width="806" height="100" viewBox="0 0 806 100">
      <polygon points="131,7 181,24 181,78 131,61" fill="var(--red)"/>
      <polygon points="181,24 232,3 232,57 181,78" fill="var(--red-dark)"/>
      <polygon points="227,0 236,0 236,8" fill="#5a0f13"/>
      <polygon points="236,0 420,0 406,29 236,29" fill="var(--red-dark)"/>
      <line x1="425" y1="13" x2="415" y2="29" stroke="#c9a9a9" stroke-width="1.5"/>
      <line x1="415" y1="28.5" x2="757" y2="28.5" stroke="var(--red)" stroke-width="1"/>
      <text x="139" y="53" font-family="Outfit, sans-serif" font-weight="600" font-size="23" fill="#fff">05</text>
      <g class="icon" transform="translate(195,24)">
        <circle cx="12" cy="6" r="5"/><circle cx="6" cy="16" r="5"/><circle cx="18" cy="16" r="5"/>
      </g>
      <line x1="406" y1="42" x2="406" y2="88" stroke="var(--red)" stroke-dasharray="1.5 3"/>
      <line x1="577" y1="42" x2="577" y2="88" stroke="var(--red)" stroke-dasharray="1.5 3"/>
    </svg>
    <div class="trait-name">Collaborator</div>
    <div class="trait-points">
      <p class="point p1">Contributes effectively and cooperatively to shared goals.</p>
      <p class="point p2">Listens actively and values diverse ideas and perspectives.</p>
      <p class="point p3">Engages respectfully, compromising and leading when appropriate.</p>
    </div>
  </div>

  <!-- 06 -->
  <div class="trait" style="top:830px">
    <svg width="806" height="100" viewBox="0 0 806 100">
      <polygon points="131,7 181,24 181,78 131,61" fill="var(--navy)"/>
      <polygon points="181,24 232,3 232,57 181,78" fill="var(--navy-light)"/>
      <polygon points="227,0 236,0 236,8" fill="#111a2c"/>
      <polygon points="236,0 420,0 406,29 236,29" fill="var(--navy)"/>
      <line x1="425" y1="13" x2="415" y2="29" stroke="#aab0c0" stroke-width="1.5"/>
      <line x1="415" y1="28.5" x2="757" y2="28.5" stroke="var(--navy)" stroke-width="1"/>
      <text x="139" y="53" font-family="Outfit, sans-serif" font-weight="600" font-size="23" fill="#fff">06</text>
      <g class="icon" transform="translate(195,24)">
        <path d="M12 20C5 15 2 11 2 7a4.5 4.5 0 0 1 10-2 4.5 4.5 0 0 1 10 2c0 4-3 8-10 13z"/>
        <path d="M0 14l4 8M24 14l-4 8"/>
      </g>
      <line x1="406" y1="42" x2="406" y2="88" stroke="var(--red)" stroke-dasharray="1.5 3"/>
      <line x1="577" y1="42" x2="577" y2="88" stroke="var(--red)" stroke-dasharray="1.5 3"/>
    </svg>
    <div class="trait-name">Compassionate</div>
    <div class="trait-points">
      <p class="point p1">Understands and acknowledges others' feelings, perspectives, and experiences.</p>
      <p class="point p2">Responds with kindness, patience, and support.</p>
      <p class="point p3">Seeks to connect with and contribute positively to the well-being of others and the community.</p>
    </div>
  </div>

  <footer class="footer">
    <span class="footer-item">
      <svg width="13" height="17" viewBox="0 0 13 17"><path d="M6.5 1a5 5 0 0 0-5 5c0 3.8 5 10 5 10s5-6.2 5-10a5 5 0 0 0-5-5z" fill="none" stroke="#fff" stroke-width="1.6"/><circle cx="6.5" cy="6" r="1.8" fill="#fff"/></svg>
      <span>Harlow Creek Public Schools 214 Maple Ridge Ave.</span>
    </span>
    <span class="footer-item">
      <svg width="15" height="15" viewBox="0 0 16 16" fill="none" stroke="#fff" stroke-width="1.1"><circle cx="8" cy="8" r="7"/><ellipse cx="8" cy="8" rx="3" ry="7"/><line x1="1" y1="8" x2="15" y2="8"/><line x1="2" y1="4.5" x2="14" y2="4.5"/><line x1="2" y1="11.5" x2="14" y2="11.5"/></svg>
      <span>www.harlowcreek-schools.example</span>
    </span>
    <span class="footer-item">
      <svg width="13" height="15" viewBox="0 0 13 15"><path d="M3 1l2.2 3.2-1.4 1.6c.8 1.8 2.2 3.3 3.9 4.2l1.5-1.5 3 2.2-1.3 2.8C6 13.2 1.2 8 1 2.3z" fill="#fff"/></svg>
      <span>555-014-2290</span>
    </span>
  </footer>
</div>
</body>
</html>
```